Business Card Design - Photographer

I am a landscape photographer and I require a business card design. 

I require two designs:
1)  a double sided business card
 and
b)  a single sided business card 

The single sided design can either be the same as the double sided (with just one side having all the information)....or it can be an entire new design. Its up to you.

My corporate colours are (CMYK):

Blue   69, 32, 0, 0
Grey  72,  64,  47,  31
Green  32,  2,  91,  0
Yellow   0, 19, 92, 0
Orange  0, 39, 75, 0

Colour space in final file should be in CMYK.

The details that need to be included on the card:

- Use the provided Logo
- Name: Wiktor Baranowski
- Email:   sales@vistalumeworks.com.au
- Website:    vistalumeworks.com.au
- Twitter:    twitter.com/vistalumeworks
- Facebook:   facebook.com/vistalumeworks
- Mobile  0417 539 662

Please use the attached template to design the logo to the specified size, including the marked bleed lines. I have also attached my logo in PNG (transparent background) and ai format for you to use.

The final file should be:
- Photoshop version with layers so I can edit the name/text etc. All non vector files should be high resolution at 1039 x 697 pixels at 300 dpi.

I also require a file as:
- Vector based PDF

Anyway questions please contact me.

Thank you

Industry/Entity Type

Landscape

Logo styles of interest
Pictorial/Combination Logo
Abstract Logo
Wordmark Logo
Lettermark Logo
Requirements
Must have
• The details that need to be included on the card:

- Use the provided Logo
- Name: Wiktor Baranowski
- Email: sales@vistalumeworks.com.au
- Website: vistalumeworks.com.au
- Twitter: twitter.com/vistalumeworks
- Facebook: facebook.com/vistalumeworks
- Mobile 0417 539 662

```html
<!DOCTYPE html>
<html lang="en">
<head>
<meta charset="utf-8">
<title>Vistalume Works – Business Cards</title>
<link rel="stylesheet" href="https://fonts.googleapis.com/css2?family=Cinzel:wght@600&family=Tinos&family=Open+Sans:wght@400&display=swap">
<style>
  :root {
    --backdrop: #e9e6e1;
    --card: #ffffff;
    --slate: #3f4254;
    --ink: #3a3a3a;
    --orange: #f5a84a;
    --rule: #c9c9c9;
    --band-text: #ffffff;
  }
  * { margin: 0; padding: 0; box-sizing: border-box; }
  html, body {
    width: 1200px; height: 401px; overflow: hidden;
    background: var(--backdrop);
  }
  .stage { position: relative; width: 1200px; height: 401px; }
  .card {
    position: absolute; top: 47px; width: 525px; height: 300px;
    background: var(--card);
    box-shadow: 0 1px 3px rgba(0,0,0,.25);
    overflow: hidden;
  }
  .card--front { left: 55px; }
  .card--back { left: 619px; }

  .brand { position: absolute; text-align: center; }
  .brand__mark {
    display: block; margin: 0 auto;
    border-radius: 50%; background: var(--slate);
  }
  .brand__name {
    display: inline-block;
    font-family: "Cinzel", "Times New Roman", serif;
    font-weight: 600; color: var(--slate);
    white-space: nowrap; letter-spacing: .5px;
    border-bottom: 1px solid var(--slate);
    line-height: 1.1;
  }
  .brand__tagline {
    font-family: "Cinzel", "Times New Roman", serif;
    font-weight: 600; color: var(--slate);
    white-space: nowrap;
  }
  .card--front .brand { left: 14px; top: 66px; width: 260px; }
  .card--front .brand__mark { width: 90px; height: 90px; margin-bottom: 14px; }
  .card--front .brand__name { font-size: 24px; padding-bottom: 2px; }
  .card--front .brand__tagline { font-size: 9.5px; letter-spacing: 1.8px; margin-top: 4px; }

  .card--back .brand { left: 0; top: 48px; width: 525px; }
  .card--back .brand__mark { width: 96px; height: 96px; margin-bottom: 20px; }
  .card--back .brand__name { font-size: 29px; padding-bottom: 3px; }
  .card--back .brand__tagline { font-size: 11.5px; letter-spacing: 2.2px; margin-top: 6px; }

  .divider {
    position: absolute; left: 283px; top: 71px;
    width: 1px; height: 137px; background: var(--rule);
  }
  .contact {
    position: absolute; left: 302px; top: 62px;
    font-family: "Tinos", "Times New Roman", serif;
    font-size: 14px; color: var(--ink); line-height: 18.5px;
    list-style: none;
  }
  .contact__person { font-weight: 700; color: var(--slate); margin-bottom: 2px; }
  .contact__address { margin-bottom: 8px; }
  .contact li { display: flex; align-items: center; }
  .contact__icon { width: 9px; height: 9px; margin-right: 5px; flex: none; }
  .contact__icon--square { background: #6a8fb8; border-radius: 1px; }

  .accent-line {
    position: absolute; left: 0; right: 0; top: 260px;
    height: 2px; background: var(--orange);
  }
  .web-band {
    position: absolute; left: 0; right: 0; bottom: 0; height: 32px;
    background: var(--slate);
    display: flex; align-items: center; justify-content: center;
    font-family: "Tinos", "Times New Roman", serif;
    font-size: 15px; letter-spacing: 3px; color: var(--band-text);
  }
  .web-plain {
    position: absolute; left: 0; width: 525px; top: 254px;
    text-align: center;
    font-family: "Open Sans", Arial, sans-serif;
    font-size: 13px; letter-spacing: 2.4px; color: var(--ink);
  }
</style>
</head>
<body>
<main class="stage">
  <section class="card card--front" aria-label="Business card front">
    <div class="brand">
      <span class="brand__mark"></span>
      <div class="brand__name">Vistalume Works</div>
      <div class="brand__tagline">FINE ART PHOTOGRAPHY</div>
    </div>
    <div class="divider"></div>
    <ul class="contact">
      <li class="contact__person">Wiktor Baranowski</li>
      <li class="contact__address">00, Complex Name<br>State Name, City 0020</li>
      <li>
        <svg class="contact__icon" viewBox="0 0 9 9" aria-hidden="true"><rect x="2" y="0.5" width="5" height="8" rx="1" fill="#555"/><rect x="3" y="1.5" width="3" height="4.5" fill="#fff"/></svg>
        0417 539 662
      </li>
      <li><span class="contact__icon contact__icon--square"></span>vistalumeworks</li>
      <li><span class="contact__icon contact__icon--square"></span>vistalumeworks</li>
      <li>
        <svg class="contact__icon" viewBox="0 0 9 9" aria-hidden="true"><rect x="0.5" y="2" width="8" height="5.5" fill="#555"/><path d="M0.5 2 L4.5 5 L8.5 2" fill="none" stroke="#fff" stroke-width=".8"/></svg>
        sales@vistalumeworks.com.au
      </li>
    </ul>
    <div class="accent-line"></div>
    <div class="web-band">www.vistalumeworks.com.au</div>
  </section>

  <section class="card card--back" aria-label="Business card back">
    <div class="brand">
      <span class="brand__mark"></span>
      <div class="brand__name">Vistalume Works</div>
      <div class="brand__tagline">FINE ART PHOTOGRAPHY</div>
    </div>
    <p class="web-plain">www.vistalumeworks.com.au</p>
  </section>
</main>
</body>
</html>
```